Need Primer (paint) Label Design

THE ATTACHED LABEL/S ARE SOLEY FOR REFERENCE. DO NOT MAKE ME AN INTERIOR PAINT OR CHALK PAINT LABEL. I ONLY NEED A "PRIMER" LABEL. THE ATTACHED INTERIOR PAINT LABEL IS ONLY TO SHOW YOU THE THEME/DESIGN OF OUR OTHER LABELS. THE BLUE LABEL ONLY HAS A DESIGN ASPECT I LIKE (PRIMER ON SIDE). The last four labels are our competitors.
```````````````````````````````````````````````````````````````````````````````````````````````````
We need this label to look professional, sharp, eye catching and modern.
OUR PRIMARY COLORS ARE BLACK AND WHITE. IF YOU INCOPORATE ANOTHER COLOR, SILVER OR GOLD MIGHT BE IDEAL BUT PLEASE DON'T DRIFT TOO FAR.
The attached documents:
1st - Our Logo
2nd - Our chalk paint label (reference). We do not need a chalk paint label.
3rd. A random design example. I like the VEYRA on the side running vertically. I think it's a cool design concept.
````````````````````````````````````````````````````````````````````````````````````````````````````
We are going to be using a normal paint can with a metal bail/handle so please use that with you design work
``````````````````````````````````````````````````````````````````````````````````````````````````
Order, in my head:
4376
Coatings
^^ I want this to stand out as well but I don't want it to be the first thing your eye is drawn to. Probably 2nd
Interior/Exterior
Multi - Surface Primer
^^ Want this to stick out and draw your eye so the customer knows what it is immediately
Exceptional Adhesion, Performance, Durability,
Use on Wood, Drywall, Plaster, Stucco, Masonry, Brick, Paneling, Painted Metal, & Properly Prepared Glossy Surfaces & More
35* Lowe Temperature Application (can be on side or small)
100% Acrylic
Low Odor - Low VOC - Soap & Water Clean Up
1 US Gallon - 3.785 L
Feel free to get creative with it!

```html
<!DOCTYPE html>
<html lang="en">
<head>
<meta charset="utf-8">
<title>4376 Coatings – Multi-Surface Primer Label</title>
<link href="https://fonts.googleapis.com/css2?family=Arimo:wght@400;700&display=swap" rel="stylesheet">
<style>
  :root {
    --backdrop: #b3b1ab;
    --ink: #111111;
    --label-black: #050505;
    --white: #ffffff;
    --silver-light: #e9e7e3;
    --silver-mid: #b9b4ad;
    --silver-dark: #6f6a64;
    --side-word: #cfcbc5;
    --pill: #222222;
  }
  * { margin: 0; padding: 0; box-sizing: border-box; }
  html, body { width: 1110px; height: 1200px; overflow: hidden; }
  body {
    background: var(--backdrop);
    font-family: "Arimo", Arial, sans-serif;
    position: relative;
  }

  .brand-name {
    position: absolute; left: 54px; top: 60px;
    color: var(--ink); font-size: 52px; font-weight: 400; line-height: 1;
    white-space: nowrap;
  }

  .label {
    position: absolute; left: 50px; top: 500px;
    width: 1010px; height: 400px;
    background: var(--label-black);
  }

  .label-side-word {
    position: absolute; left: 300px; top: 30px;
    width: 84px; height: 340px;
  }
  .label-side-word span {
    position: absolute; left: 50%; top: 50%;
    transform: translate(-50%, -50%) rotate(-90deg);
    color: var(--side-word); font-size: 88px; font-weight: 400; line-height: 1;
    white-space: nowrap;
  }

  .label-panel {
    position: absolute; left: 388px; top: 32px; width: 235px;
  }
  .panel-brand {
    height: 122px;
    border: 1px solid var(--silver-dark); border-bottom: none;
    display: flex; align-items: center; justify-content: center;
    color: var(--white); font-size: 30px; font-weight: 400; line-height: 1;
    white-space: nowrap;
  }

  .panel-product {
    height: 124px;
    background: linear-gradient(100deg, var(--silver-dark) 0%, var(--silver-light) 38%, var(--silver-mid) 62%, var(--silver-light) 80%, var(--silver-dark) 100%);
    border-radius: 0 0 44px 44px;
    text-align: center; color: var(--ink); font-weight: 700; line-height: 1.12;
    padding-top: 14px;
  }
  .panel-product .line-use { font-size: 17px; }
  .panel-product .line-kind { font-size: 15px; letter-spacing: 2px; }
  .panel-product .line-name { font-size: 22px; }

  .acrylic-pill {
    width: 124px; height: 24px; margin: 3px auto 0;
    background: var(--pill); border: 1px solid var(--silver-mid); border-radius: 3px;
    color: var(--white); font-size: 13px; font-weight: 700;
    display: flex; align-items: center; justify-content: center;
  }

  .spec-table {
    display: flex; margin-top: 10px;
    border: 1px solid var(--silver-mid); color: var(--white);
  }
  .spec-size {
    width: 44px; text-align: center; font-size: 8px; font-weight: 700; line-height: 1.05;
    padding-top: 2px; border-right: 1px solid var(--silver-mid);
  }
  .spec-size .litres {
    display: block; margin-top: 2px; border-top: 1px solid var(--silver-mid);
    background: var(--white); color: var(--ink); padding: 1px 0;
  }
  .spec-details { flex: 1; text-align: center; white-space: nowrap; overflow: hidden; }
  .spec-details .benefits {
    font-size: 6.2px; font-weight: 700; padding: 2px 0;
    border-bottom: 1px solid var(--silver-mid);
  }
  .spec-details .surfaces { font-size: 5.2px; font-weight: 700; line-height: 1.4; padding: 2px 1px; }

  .footnote {
    display: flex; align-items: center; gap: 4px; margin-top: 4px;
    color: var(--white); white-space: nowrap;
  }
  .footnote .temp { font-size: 4.8px; font-weight: 400; }
  .footnote .divider { width: 1px; height: 8px; background: var(--silver-mid); }
  .footnote .care { font-size: 6.2px; font-weight: 700; color: var(--white); }
</style>
</head>
<body>

  <div class="brand-name">4376 Coatings</div>

  <section class="label">
    <div class="label-side-word"><span>Veyra</span></div>

    <div class="label-panel">
      <div class="panel-brand">4376 Coatings</div>
      <div class="panel-product">
        <div class="line-use">INTERIOR/EXTERIOR</div>
        <div class="line-kind">MULTI - SURFACE</div>
        <div class="line-name">PRIMER</div>
      </div>
      <div class="acrylic-pill">100% Acrylic</div>

      <div class="spec-table">
        <div class="spec-size">1 US<br>Gallon<span class="litres">3.785 L</span></div>
        <div class="spec-details">
          <div class="benefits">EXCEPTIONAL ADHESION | PERFORMANCE | DURABILITY</div>
          <div class="surfaces">Use on Wood | Drywall | Plaster | Stucco | Masonry | Brick<br>Paneling | Painted Metal | &amp; Properly Prepared Glossy Surfaces &amp; More</div>
        </div>
      </div>

      <div class="footnote">
        <span class="temp">35+ Low Temperature Application</span>
        <span class="divider"></span>
        <span class="care">Low Odor - Low VOC - Soap &amp; Water Clean Up</span>
      </div>
    </div>
  </section>

</body>
</html>
```